Hvac and insulation company needs good looking business card design

We are hvac and insulation company and looking for a new business cards that look to today standards designs

Target Market(s)

homeowners

Industry/Entity Type

Hvac

Contact Information for Business Card

Name: Walter Brinoku
Home comfort consultant
address: 4827 Dunmore St #215 Oakland, CA 94619
office: 888-316-2790
cell: 510-742-3185
Lic.# 584261
Email: walter@corvane-hvac.com
Web: corvane-hvac.com

Requirements
Must have
• clean and sleek look
Nice to have
• simple with a clean look
Should not have
• to busy business card

```html
<!DOCTYPE html>
<html lang="en">
<head>
<meta charset="utf-8">
<title>Corvane Home Solutions – Business Card</title>
<link href="https://fonts.googleapis.com/css2?family=Open+Sans:wght@400;600&display=swap" rel="stylesheet">
<style>
  :root {
    --orange: #e57a1f;
    --grey: #6b6c6c;
    --grey-dark: #5e5f5f;
    --grey-light: #c9c9c9;
    --white: #ffffff;
    --paper: #fbfbfb;
    --backdrop: #e6e7e8;
  }
  * { box-sizing: border-box; margin: 0; padding: 0; }
  html, body {
    width: 1200px; height: 900px; overflow: hidden;
    background: var(--backdrop);
    font-family: "Open Sans", Arial, sans-serif;
  }
  .sheet {
    width: 1200px; height: 900px;
    display: flex; flex-direction: column;
    align-items: center; justify-content: center; gap: 50px;
  }
  .card {
    position: relative;
    width: 640px; height: 380px;
    border-radius: 18px;
    overflow: hidden;
    box-shadow: 0 10px 28px rgba(0,0,0,.18);
  }
  .card-front { background: linear-gradient(160deg, var(--white) 0%, #efefef 100%); }
  .card-back { background: var(--grey); }
  .card-art { position: absolute; inset: 0; width: 100%; height: 100%; }

  .brand {
    position: absolute; left: 40px; top: 40px;
    display: flex; align-items: center; gap: 12px;
    color: var(--orange); font-weight: 600;
  }
  .brand-mark { width: 26px; height: 26px; background: var(--orange); border-radius: 50%; }
  .brand-name { font-size: 30px; line-height: 1; letter-spacing: .5px; }
  .brand-name small { display: block; font-size: 13px; letter-spacing: 3px; margin-top: 4px; }

  .person {
    position: absolute; right: 42px; top: 130px; text-align: right;
  }
  .person-name {
    color: var(--orange); font-size: 26px; font-weight: 600;
    text-transform: uppercase; letter-spacing: .5px; line-height: 1.1;
  }
  .person-title { color: var(--grey); font-size: 15px; margin-top: 2px; }

  .contact {
    position: absolute; right: 86px; top: 248px;
    list-style: none; text-align: right;
    color: var(--white); font-size: 14px; line-height: 18px;
  }
  .contact li { position: relative; }
  .contact .gap { margin-top: 8px; }
  .contact svg {
    position: absolute; right: -22px; top: 3px; width: 12px; height: 12px;
    fill: none; stroke: var(--white); stroke-width: 1.6;
  }

  .back-brand {
    position: absolute; inset: 0;
    display: flex; flex-direction: column; align-items: center; justify-content: center;
  }
  .back-brand .brand { position: static; }
  .back-brand .brand-mark { width: 40px; height: 40px; }
  .back-brand .brand-name { font-size: 52px; }
  .back-brand .brand-name small { font-size: 20px; letter-spacing: 5px; }
  .license { color: var(--grey-light); font-size: 18px; margin-top: 34px; letter-spacing: 1px; }
</style>
</head>
<body>
<main class="sheet">

  <section class="card card-front" aria-label="Card front">
    <svg class="card-art" viewBox="0 0 640 380" aria-hidden="true">
      <path fill="var(--orange)" d="M0,92 C60,150 170,180 300,186 C190,188 70,168 0,112 Z"/>
      <path fill="var(--grey)" d="M0,128 C130,190 320,200 430,206 C520,212 585,245 620,300 C570,252 500,226 420,220 C300,212 110,200 0,138 Z"/>
      <path fill="var(--grey-dark)" d="M0,150 C120,205 280,215 380,218 C470,222 530,232 580,265 C610,285 630,315 640,340 L640,380 L0,380 Z"/>
    </svg>

    <div class="brand">
      <span class="brand-mark"></span>
      <span class="brand-name">corvane<small>home solutions</small></span>
    </div>

    <div class="person">
      <p class="person-name">Walter Brinoku</p>
      <p class="person-title">Home comfort consultant</p>
    </div>

    <ul class="contact">
      <li>4827 Dunmore St</li>
      <li>#215 Oakland, CA 94619</li>
      <li class="gap">888-316-2790
        <svg viewBox="0 0 12 12"><path d="M2,1 L4.5,1 L5.5,4 L4,5 C5,7 6,8 7,8.5 L8,7 L11,8 L11,10.5 C6,11 1,6 2,1 Z"/></svg></li>
      <li>510-742-3185
        <svg viewBox="0 0 12 12"><rect x="3" y="0.8" width="6" height="10.4" rx="1"/><path d="M5,9.5 H7"/></svg></li>
      <li>walter@corvane-hvac.com
        <svg viewBox="0 0 12 12"><rect x="1" y="2.5" width="10" height="7"/><path d="M1,2.5 L6,6.5 L11,2.5"/></svg></li>
      <li>www.corvane-hvac.com
        <svg viewBox="0 0 12 12"><circle cx="6" cy="6" r="5"/><path d="M1,6 H11 M6,1 C3.5,4 3.5,8 6,11 M6,1 C8.5,4 8.5,8 6,11"/></svg></li>
    </ul>
  </section>

  <section class="card card-back" aria-label="Card back">
    <div class="back-brand">
      <div class="brand">
        <span class="brand-mark"></span>
        <span class="brand-name">corvane<small>home solutions</small></span>
      </div>
      <p class="license">Lic.# 584261</p>
    </div>
  </section>

</main>
</body>
</html>
```